Banner for construction site to identify developer

we need a 4 foot by 8 foot banner to hang on the fence of a residential townhome development in Phoenix, Arizona that identifies Tolvane Holdings as the company behind the development/project. Also needs to include the logo, phone number, and web address. Would like to stick with the blue colors provided in the attached logo. The blues should stay the same but the letters in the logo can change to another color if necessary. Feel free to use "Tolvane Holdings" in place of "Tolvane Holdings Group". Looking for use of colors/design to take up space so banner is not just text with a logo.

Target Market(s)

drive by traffic looking at the site

Industry/Entity Type

Real Estate

Colors
0054AA
0677BA
7BADD7
CADEEF
E8F1F8

Requirements
Must have
• company name, phone number and web address

```html
<!DOCTYPE html>
<html lang="en">
<head>
<meta charset="utf-8">
<title>Tolvane Holdings – Development Site Banner</title>
<link rel="stylesheet" href="https://fonts.googleapis.com/css2?family=Poppins:wght@500;600;700&display=swap">
<style>
  :root {
    --page-bg: #f4f5f6;
    --navy-strip: #1d6c9f;
    --band-blue: #1c70a2;
    --sky-blue: #19a8dc;
    --panel-light: #e8eaec;
    --panel-mist: #cfd6dc;
    --ink: #3a3a3c;
    --white: #ffffff;
  }
  * { margin: 0; padding: 0; box-sizing: border-box; }
  html, body {
    width: 1200px;
    height: 1200px;
    overflow: hidden;
    background: var(--page-bg);
    font-family: "Poppins", sans-serif;
  }
  .canvas {
    width: 1200px;
    height: 1200px;
    display: flex;
    align-items: center;
    justify-content: center;
  }
  .banner {
    width: 1120px;
    height: 585px;
    display: flex;
    flex-direction: column;
    box-shadow: 0 6px 18px rgba(0,0,0,0.12);
  }
  .banner__top-strip {
    height: 15px;
    background: var(--navy-strip);
  }
  .banner__hero {
    position: relative;
    height: 294px;
    background: var(--panel-light);
    overflow: hidden;
  }
  .hero__skyline {
    position: absolute;
    inset: 0;
    background: linear-gradient(100deg, #eef0f2 0%, #e3e7ea 35%, #d6dde2 70%, #dfe4e8 100%);
  }
  .hero__location {
    position: absolute;
    top: 18px;
    right: 20px;
    font-size: 17px;
    font-weight: 600;
    letter-spacing: 0.06em;
    color: var(--ink);
  }
  .hero__brand {
    position: absolute;
    left: 0;
    right: 0;
    top: 150px;
    display: flex;
    align-items: center;
    justify-content: center;
    gap: 22px;
  }
  .brand__square {
    width: 62px;
    height: 62px;
    background: var(--sky-blue);
  }
  .brand__name {
    font-size: 76px;
    font-weight: 700;
    color: var(--ink);
    letter-spacing: -0.01em;
    line-height: 1;
  }
  .banner__title-band {
    height: 87px;
    background: var(--band-blue);
    display: flex;
    align-items: center;
    justify-content: center;
  }
  .title-band__text {
    color: var(--white);
    font-size: 54px;
    font-weight: 700;
    letter-spacing: 0.2em;
    padding-left: 0.2em;
  }
  .banner__divider {
    height: 14px;
    background: linear-gradient(var(--sky-blue) 0 5px, var(--band-blue) 5px 8px, var(--sky-blue) 8px);
  }
  .banner__contact {
    height: 147px;
    background: var(--sky-blue);
    display: flex;
    flex-direction: column;
    align-items: center;
    justify-content: center;
    gap: 14px;
    color: var(--white);
  }
  .contact__line {
    font-size: 32px;
    font-weight: 500;
    letter-spacing: 0.08em;
    line-height: 1;
  }
  .contact__label { font-weight: 700; }
  .banner__bottom-strip {
    height: 28px;
    background: var(--navy-strip);
  }
</style>
</head>
<body>
  <main class="canvas">
    <section class="banner">
      <div class="banner__top-strip"></div>
      <div class="banner__hero">
        <div class="hero__skyline" role="img" aria-label="Faded photograph of a city skyline with high-rise buildings"></div>
        <p class="hero__location">Phoenix, Arizona</p>
        <div class="hero__brand">
          <span class="brand__square"></span>
          <h1 class="brand__name">Tolvane Holdings</h1>
        </div>
      </div>
      <div class="banner__title-band">
        <h2 class="title-band__text">DEVELOPMENT SITE</h2>
      </div>
      <div class="banner__divider"></div>
      <div class="banner__contact">
        <p class="contact__line"><span class="contact__label">PHONE:</span> (602) 555-0148</p>
        <p class="contact__line"><span class="contact__label">WEB:</span> WWW.TOLVANEHOLDINGSGROUP.COM</p>
      </div>
      <div class="banner__bottom-strip"></div>
    </section>
  </main>
</body>
</html>
```